Marwick Law Letterhead

We need a new letterhead design for a Law Firm. The address for the law firm is 1475 Calloway Street, Suite 210, Houston, Texas 77041. Phone Number: 832-361-9027; Fax Number: 832-614-7359. The logo is uploaded to the project.

```html
<!DOCTYPE html>
<html lang="en">
<head>
<meta charset="utf-8">
<title>Marwick Law Letterhead</title>
<link href="https://fonts.googleapis.com/css2?family=Tinos:wght@400&display=swap" rel="stylesheet">
<style>
  :root {
    --backdrop: #e4e5e8;
    --paper: #ffffff;
    --navy: #27315f;
    --red: #e0241f;
    --ink: #2b3566;
    --faint-ring: #ecedf2;
  }
  * { margin: 0; padding: 0; box-sizing: border-box; }
  html, body {
    width: 1200px;
    height: 1200px;
    overflow: hidden;
    background: var(--backdrop);
  }
  .letterhead {
    position: absolute;
    left: 190px;
    top: 20px;
    width: 820px;
    height: 1160px;
    background: var(--paper);
    overflow: hidden;
    font-family: "Tinos", "Times New Roman", serif;
  }
  .brand {
    position: absolute;
    left: 41px;
    top: 58px;
    display: flex;
    align-items: center;
    gap: 12px;
  }
  .brand-mark {
    width: 30px;
    height: 30px;
    border-radius: 50%;
    background: var(--navy);
  }
  .brand-name {
    font-size: 36px;
    line-height: 1;
    color: var(--navy);
    font-weight: 400;
  }
  .contact {
    position: absolute;
    left: 598px;
    top: 45px;
    color: var(--ink);
    font-size: 13.5px;
    line-height: 17px;
  }
  .contact-line {
    display: flex;
    align-items: center;
    gap: 6px;
  }
  .contact-line svg { width: 11px; height: 11px; fill: var(--red); }
  .address { margin-top: 4px; }
  .header-rule {
    position: absolute;
    left: 39px;
    top: 125px;
    width: 742px;
    height: 2px;
    background: var(--navy);
  }
  .header-rule::before {
    content: "";
    position: absolute;
    left: 0;
    top: -1px;
    width: 214px;
    height: 3px;
    background: var(--red);
  }
  .corner-ring {
    position: absolute;
    left: 0;
    bottom: 0;
    width: 400px;
    height: 470px;
  }
</style>
</head>
<body>
  <main class="letterhead">
    <header>
      <div class="brand">
        <span class="brand-mark" aria-hidden="true"></span>
        <span class="brand-name">Marwick Law</span>
      </div>
      <address class="contact">
        <div class="contact-line">
          <svg viewBox="0 0 24 24" aria-label="Phone"><path d="M6.6 10.8a15.1 15.1 0 0 0 6.6 6.6l2.2-2.2c.3-.3.7-.4 1-.2 1.1.4 2.3.6 3.6.6.6 0 1 .4 1 1V20c0 .6-.4 1-1 1A17 17 0 0 1 3 4c0-.6.4-1 1-1h3.5c.6 0 1 .4 1 1 0 1.3.2 2.5.6 3.6.1.3 0 .7-.2 1z"/></svg>
          <span>832-361-9027</span>
        </div>
        <div class="contact-line">
          <svg viewBox="0 0 24 24" aria-label="Fax"><path d="M6 2h12v6H6z M3 9h18v9h-3v-4H6v4H3z M7 15h10v7H7z"/></svg>
          <span>832-614-7359</span>
        </div>
        <div class="address">1475 Calloway Street<br>Suite 210, Houston, Texas 77041</div>
      </address>
      <div class="header-rule"></div>
    </header>
    <svg class="corner-ring" viewBox="0 0 400 470" aria-hidden="true">
      <circle cx="138" cy="250" r="210" fill="none" stroke="var(--faint-ring)" stroke-width="40"/>
    </svg>
  </main>
</body>
</html>
```